Summit Ridge Business Card

Side 1: Summit Ridge Logo (logo without Maltese cross) with industrial rope rescue related theme. Our company services - TRAINING - Fire Training, Confined Space Rescue Training, Rope Rescue training, Hazmat Training, Incident Command, EMS, Pump Operations Training. Website - summitridgeexample.com.
Side 2: Summit Ridge Fire Department Logo (logo with Maltese cross) with Firefighter related theme. Company (division) services - FIELD SERVICES - Fire Department, Stand-by Rescue, Safety, EMS, Planning. "Supporting the Emergency Response Community Since 1967"

Add contact information wherever it makes since (Name, Email, Phone).
I would like it to represent the Summit Ridge Fire Department Logo as a division not as a separate entity without saying it, possibly by depicting it in the background of Side 2 instead of being a standalone picture like the logo on Side 1.

```html
<!DOCTYPE html>
<html lang="en">
<head>
<meta charset="utf-8">
<title>Summit Ridge Business Card</title>
<link href="https://fonts.googleapis.com/css2?family=Roboto:wght@400;500;700&display=swap" rel="stylesheet">
<style>
  :root {
    --page-bg: #e9e6e2;
    --card-bg: #f4f4f4;
    --brand-red: #e2141b;
    --heading-red: #d9342a;
    --ink: #333333;
    --ink-soft: #444444;
    --mark-faint: rgba(226, 20, 27, 0.08);
    --mark-faint-text: rgba(226, 20, 27, 0.12);
  }
  * { margin: 0; padding: 0; box-sizing: border-box; }
  html, body {
    width: 1200px; height: 1040px; overflow: hidden;
    background: var(--page-bg);
    font-family: "Roboto", Arial, sans-serif;
    color: var(--ink);
  }
  .canvas { position: relative; width: 1200px; height: 1040px; }
  .card {
    position: absolute;
    background: var(--card-bg);
    border-radius: 16px;
    box-shadow: 0 2px 4px rgba(0,0,0,0.18);
    overflow: hidden;
  }
  .card--front { left: 285px; top: 130px; width: 640px; height: 365px; }
  .card--back  { left: 284px; top: 567px; width: 646px; height: 369px; }

  /* Front */
  .brand {
    position: absolute; right: 46px; top: 86px;
    display: flex; align-items: center; gap: 10px;
  }
  .brand__square { width: 16px; height: 16px; background: var(--brand-red); }
  .brand__name {
    font-weight: 700; font-size: 26px; letter-spacing: 0.5px;
    color: var(--brand-red);
  }
  .person { position: absolute; left: 27px; top: 198px; }
  .person__name {
    font-weight: 500; font-size: 23px; color: var(--brand-red);
    line-height: 1.1; margin-bottom: 2px;
  }
  .person__line { font-size: 16px; line-height: 20px; color: var(--ink); }
  .person__title { padding-left: 2px; }
  .contact { position: absolute; left: 264px; top: 203px; list-style: none; }
  .contact li { font-size: 16px; line-height: 20px; color: var(--ink); }
  .contact__label { color: var(--brand-red); font-weight: 500; margin-right: 3px; }
  .training {
    position: absolute; left: 28px; top: 300px; width: 600px;
    font-size: 14px; line-height: 17.5px; color: var(--ink-soft);
  }

  /* Back */
  .division-mark { position: absolute; left: 12px; top: 21px; width: 320px; height: 320px; }
  .services { position: absolute; left: 372px; top: 82px; }
  .services__title {
    font-weight: 700; font-size: 24px; letter-spacing: 0.6px;
    color: var(--heading-red); margin-bottom: 19px;
  }
  .services__list { list-style: none; }
  .services__list li {
    font-size: 16px; line-height: 20px; letter-spacing: 0.5px; color: var(--ink);
    position: relative; padding-left: 14px;
  }
  .services__list li::before {
    content: ""; position: absolute; left: 0; top: 8px;
    width: 5px; height: 5px; border-radius: 50%; background: var(--brand-red);
  }
  .services__tagline {
    margin-top: 19px; font-size: 14.5px; line-height: 18px;
    letter-spacing: 0.5px; color: var(--ink);
  }
</style>
</head>
<body>
<main class="canvas">

  <section class="card card--front" aria-label="Business card front">
    <div class="brand">
      <span class="brand__square" aria-hidden="true"></span>
      <span class="brand__name">SUMMIT RIDGE</span>
    </div>

    <div class="person">
      <h1 class="person__name">DANIEL HARPER</h1>
      <p class="person__line person__title">President</p>
      <p class="person__line">418 Cedar Point Dr., Beaumont</p>
      <p class="person__line">TX, United States, 77701</p>
    </div>

    <ul class="contact">
      <li><span class="contact__label">P :</span>+1 409-555-0148</li>
      <li><span class="contact__label">C :</span>+1 409-555-0148</li>
      <li><span class="contact__label">E :</span>daniel@srexample.com</li>
      <li><span class="contact__label">W :</span>www.summitridgeexample.com</li>
    </ul>

    <p class="training">TRAINING - Fire Training, Confined Space Rescue Training, Rope Rescue training<br>Hazmat Training, Incident Command, EMS, Pump Operations Training.</p>
  </section>

  <section class="card card--back" aria-label="Business card back">
    <svg class="division-mark" viewBox="0 0 320 320" role="img" aria-label="Faint Summit Ridge Fire Department division mark">
      <circle cx="160" cy="160" r="150" fill="var(--mark-faint)"/>
      <text x="160" y="170" text-anchor="middle" font-family="Roboto, Arial, sans-serif" font-weight="700" font-size="32" fill="var(--mark-faint-text)">SUMMIT RIDGE</text>
    </svg>

    <div class="services">
      <h2 class="services__title">FIELD SERVICES</h2>
      <ul class="services__list">
        <li>Fire Department</li>
        <li>Stand-by Rescue</li>
        <li>Safety</li>
        <li>EMS</li>
        <li>Planning</li>
      </ul>
      <p class="services__tagline">Supporting the Emergency<br>Response Community<br>Since 1967</p>
    </div>
  </section>

</main>
</body>
</html>
```